Equipment Finance Specialist I work with companies who need the funds to buy their equipment

I would like a business card that stands out on the shelves. I want to be able to hand it to someone and say WOW. This card should have my logo.
You can put color into it I am very open on design and color

What my company does is we deal with dealerships that sell equipment such as Dump Trucks garbage trucks tractors trailers. Customers get referred to us and depending on their time in business we will ask for the following items

Companies that have been in business for more than two years we have a credit application program up to 250K . With this program we need the following items Credit application filled out(which is what I would like to be able for the customer to click on my website to get.) as well as three current month bank statements.

Deals over 250k we will need the following items

2 years business tax returns
2 years personal tax returns
Profit & Loss statement
Personal Financial Statement

what we do
100% FINANCING
SEASONAL PAYMENTS
LOAN BALLOON PAYMENTS
TRAC LEASING
LOW-INTEREST REFINANCING RATES
DEBT CONSOLIDATION

We specialize in creative financing solutions and offer a variety of reliable, flexible and expandable lending choices.

Target Market(s)

Trucking Companies

Industry/Entity Type

Trucking Company

Contact Information for Business Card

* $250,000 Application only Program
* Loans from $30,000 to 5,000,000
* Competitive Interest Rates

Font styles to use
Serif
Sans Serif

Colors

Designer to choose colors to be used in the design.

Requirements
Must have
• On the back of the card.
• * $250,000 Application only Program
• * Loans from $30,000 to 5,000,000
• My name, email, website. address
• * Competitive Interest Rates
• * 100% Financing
Nice to have
• I want my logo to pop on the card
• My logo is the great one I would like to use
Should not have
• I am up for your creativity as well

```html
<!DOCTYPE html>
<html lang="en">
<head>
<meta charset="utf-8">
<title>Summit Lending Business Card</title>
<link rel="stylesheet" href="https://fonts.googleapis.com/css2?family=Work+Sans:wght@400;500;700&display=swap">
<style>
  :root {
    --backdrop: #1c1c1e;
    --card: #232325;
    --card-edge: #2c2c2f;
    --accent-red: #e3202f;
    --accent-blue: #22338a;
    --text-light: #f2f2f2;
    --text-muted: #c9c9cc;
    --divider: #e6e6e6;
  }
  * { box-sizing: border-box; margin: 0; padding: 0; }
  html, body {
    width: 1200px;
    height: 900px;
    overflow: hidden;
    background: var(--backdrop);
    font-family: "Work Sans", Arial, sans-serif;
  }
  .canvas {
    position: relative;
    width: 1200px;
    height: 900px;
  }
  .card {
    position: absolute;
    left: 240px;
    width: 720px;
    height: 412px;
    background: linear-gradient(135deg, var(--card) 0%, var(--card-edge) 100%);
    border-bottom: 7px solid var(--accent-red);
    box-shadow: 0 18px 40px rgba(0, 0, 0, 0.55);
  }
  .card--front { top: 24px; }
  .card--back { top: 464px; }

  .brand {
    display: flex;
    align-items: center;
    gap: 18px;
  }
  .brand__mark {
    width: 58px;
    height: 58px;
    border-radius: 50%;
    background: var(--accent-blue);
    flex: none;
  }
  .brand__name {
    color: var(--accent-red);
    font-weight: 700;
    font-size: 40px;
    letter-spacing: 2px;
    line-height: 1;
    text-transform: uppercase;
  }
  .brand__line { display: block; }

  .card--front .brand {
    position: absolute;
    left: 50%;
    top: 88px;
    transform: translateX(-50%);
  }

  .offers {
    position: absolute;
    left: 80px;
    right: 80px;
    top: 268px;
    display: grid;
    grid-template-columns: 1fr 1fr;
    column-gap: 32px;
    row-gap: 14px;
    list-style: none;
    color: var(--text-muted);
    font-size: 15px;
    letter-spacing: 0.8px;
  }
  .offers li {
    display: flex;
    align-items: center;
    gap: 10px;
    white-space: nowrap;
  }
  .offers li::before {
    content: "";
    width: 7px;
    height: 7px;
    background: var(--accent-red);
    flex: none;
  }

  .card--back .brand {
    position: absolute;
    left: 48px;
    top: 160px;
    gap: 14px;
  }
  .card--back .brand__mark { width: 46px; height: 46px; }
  .card--back .brand__name { font-size: 30px; }

  .divider {
    position: absolute;
    left: 378px;
    top: 96px;
    width: 2px;
    height: 218px;
    background: var(--divider);
  }
  .contact {
    position: absolute;
    left: 410px;
    top: 92px;
    color: var(--text-light);
  }
  .contact__name {
    color: var(--accent-red);
    font-weight: 500;
    font-size: 27px;
    letter-spacing: 1.5px;
    text-transform: uppercase;
  }
  .contact__title {
    font-size: 18px;
    letter-spacing: 1px;
    margin-top: 2px;
  }
  .contact__address {
    font-size: 18px;
    letter-spacing: 1.2px;
    line-height: 1.35;
    margin-top: 24px;
  }
  .contact__list {
    list-style: none;
    margin-top: 18px;
    font-size: 18px;
    letter-spacing: 1.2px;
  }
  .contact__list li {
    display: flex;
    align-items: center;
    gap: 12px;
    height: 28px;
  }
  .contact__icon {
    width: 14px;
    height: 14px;
    flex: none;
  }
  .contact__highlight { color: var(--accent-red); }
</style>
</head>
<body>
<main class="canvas">
  <section class="card card--front" aria-label="Card front">
    <div class="brand">
      <span class="brand__mark"></span>
      <span class="brand__name"><span class="brand__line">Summit</span><span class="brand__line">Lending</span></span>
    </div>
    <ul class="offers">
      <li>$250,000 Application Only Program</li>
      <li>Loans from $30,000 to $5,000,000</li>
      <li>Competitive Interest Rates</li>
      <li>100% Financing</li>
    </ul>
  </section>

  <section class="card card--back" aria-label="Card back">
    <div class="brand">
      <span class="brand__mark"></span>
      <span class="brand__name"><span class="brand__line">Summit</span><span class="brand__line">Lending</span></span>
    </div>
    <div class="divider"></div>
    <div class="contact">
      <p class="contact__name">Daniel Reyes</p>
      <p class="contact__title">Director</p>
      <p class="contact__address">1180 Ridgeline Dr.<br>Austin, TX 78701</p>
      <ul class="contact__list">
        <li>
          <svg class="contact__icon" viewBox="0 0 24 24" aria-hidden="true">
            <path d="M6.6 10.8a15.1 15.1 0 0 0 6.6 6.6l2.2-2.2a1 1 0 0 1 1-.25 11.4 11.4 0 0 0 3.6.57 1 1 0 0 1 1 1V20a1 1 0 0 1-1 1A17 17 0 0 1 3 4a1 1 0 0 1 1-1h3.5a1 1 0 0 1 1 1c0 1.25.2 2.45.57 3.57a1 1 0 0 1-.25 1z" fill="var(--accent-red)"/>
          </svg>
          1400 622 910
        </li>
        <li>
          <svg class="contact__icon" viewBox="0 0 24 24" aria-hidden="true">
            <rect x="2.5" y="5" width="19" height="14" rx="1.5" fill="none" stroke="var(--accent-red)" stroke-width="2"/>
            <path d="M3 6l9 7 9-7" fill="none" stroke="var(--accent-red)" stroke-width="2"/>
          </svg>
          info@summitlending.com
        </li>
        <li>
          <svg class="contact__icon" viewBox="0 0 24 24" aria-hidden="true">
            <circle cx="12" cy="12" r="9.5" fill="none" stroke="var(--accent-red)" stroke-width="2"/>
            <ellipse cx="12" cy="12" rx="4" ry="9.5" fill="none" stroke="var(--accent-red)" stroke-width="1.6"/>
            <path d="M2.5 12h19" stroke="var(--accent-red)" stroke-width="1.6"/>
          </svg>
          <span>www.<span class="contact__highlight">summitlending</span>.com</span>
        </li>
      </ul>
    </div>
  </section>
</main>
</body>
</html>
```